Bram Keystone Homes needs a business card

We need a business card for a new company in Canada, Ontario. Our company is all about luxury contraction homes for our clients. Our product and services are custom projects design. Under the business logo that will be created, we want a slogan that will be a memorable phrase for consumers to remember us to tell their friends and relatives.

Additional infomation
- Ludovic Entrasse
- President / Ceo
-519.604.3087

Find point what luxury construction products and services can be done

We like to see colors:
- #663300
- and something other colors or color that would attract the client needs and wants

The final design should communicate leads from new or old clients that will grow our empire. Most of all, we try to work among the budget that clients want

NOTE
- we also need an icon for the business (Example: Instagram, Facebook, and Whatsapp icons)
- We want the company name to be remembered easily for clients and our distributors who would get our orders.
- we need an icon on the business cards: Facebook and Instagram.

Thanks,
Bram Keystone Homes

```html
<!DOCTYPE html>
<html lang="en">
<head>
<meta charset="UTF-8">
<title>Bram Keystone Homes — Business Card</title>
<link href="https://fonts.googleapis.com/css2?family=Work+Sans:wght@400;500;600;700&display=swap" rel="stylesheet">
<style>
  :root {
    --brand-brown: #663300;
    --card-brown: #6a3b1b;
    --paper: #ffffff;
    --ink: #3c3c3c;
    --backdrop: #1a1a1a;
  }
  * { box-sizing: border-box; margin: 0; padding: 0; }
  html, body {
    width: 1200px; height: 900px; overflow: hidden;
    background: var(--backdrop);
    font-family: "Work Sans", Arial, sans-serif;
  }
  .canvas {
    width: 1200px; height: 900px;
    display: flex; flex-direction: column;
    align-items: center; justify-content: center; gap: 40px;
  }
  .card {
    width: 700px; height: 400px; position: relative;
    box-shadow: 0 10px 30px rgba(0,0,0,.5);
  }
  /* Front */
  .card-front {
    background: var(--card-brown);
    display: flex; flex-direction: column;
    align-items: center; justify-content: center;
    color: var(--paper);
  }
  .brand-name { font-weight: 700; letter-spacing: -0.5px; line-height: 1; }
  .card-front .brand-name { font-size: 40px; }
  .brand-tagline { font-weight: 600; text-transform: uppercase; letter-spacing: .3px; }
  .card-front .brand-tagline { font-size: 14px; margin-top: 8px; }

  /* Back */
  .card-back { background: var(--paper); color: var(--ink); }
  .back-brand {
    position: absolute; left: 36px; top: 32px;
    color: var(--brand-brown);
  }
  .back-brand .brand-name { font-size: 30px; }
  .back-brand .brand-tagline { font-size: 11px; margin-top: 4px; }
  .social-links {
    position: absolute; right: 48px; top: 40px;
    display: flex; gap: 10px; list-style: none;
  }
  .social-links li {
    width: 24px; height: 24px; border-radius: 50%;
    background: var(--brand-brown);
  }
  .holder { position: absolute; right: 48px; top: 190px; text-align: right; }
  .holder-name { font-size: 27px; font-weight: 600; color: var(--brand-brown); letter-spacing: .5px; }
  .holder-role { font-size: 19px; letter-spacing: 1px; margin-top: 4px; }
  .divider-rule {
    position: absolute; left: 36px; right: 48px; top: 276px;
    height: 1.5px; background: var(--brand-brown);
  }
  .contact-list {
    position: absolute; left: 36px; top: 294px; list-style: none;
    font-size: 19px; line-height: 28px; letter-spacing: .5px;
  }
  .contact-list li { display: flex; align-items: center; gap: 12px; }
  .contact-list svg { width: 14px; height: 14px; flex: none; }
  .address {
    position: absolute; right: 48px; bottom: 30px; text-align: right;
    font-size: 19px; line-height: 28px; letter-spacing: 1px; font-style: normal;
  }
</style>
</head>
<body>
<main class="canvas">
  <section class="card card-front">
    <h1 class="brand-name">Bram Keystone Homes</h1>
    <p class="brand-tagline">- Home Renovations - Custom Project Design -</p>
  </section>

  <section class="card card-back">
    <div class="back-brand">
      <p class="brand-name">Bram Keystone Homes</p>
      <p class="brand-tagline">- Home Renovations - Custom Project Design -</p>
    </div>

    <ul class="social-links">
      <li role="img" aria-label="Social network profile icon"></li>
      <li role="img" aria-label="Photo sharing profile icon"></li>
    </ul>

    <div class="holder">
      <p class="holder-name">Ludovic Entrasse</p>
      <p class="holder-role">President / Ceo</p>
    </div>

    <div class="divider-rule"></div>

    <ul class="contact-list">
      <li>
        <svg viewBox="0 0 16 16" aria-hidden="true"><path d="M4 1.5l2.2 3-1.4 1.6c.8 1.9 2.2 3.3 4.1 4.1l1.6-1.4 3 2.2-1.2 2.6C7.5 13.5 2.5 8.5 1.4 2.7z" fill="none" stroke="#663300" stroke-width="1.4" stroke-linejoin="round"/></svg>
        519.604.3087
      </li>
      <li>
        <svg viewBox="0 0 16 16" aria-hidden="true"><rect x="1.5" y="3.5" width="13" height="9" fill="none" stroke="#663300" stroke-width="1.4"/><path d="M1.5 3.5L8 9l6.5-5.5" fill="none" stroke="#663300" stroke-width="1.4"/></svg>
        info@bramkeystone.com
      </li>
      <li>
        <svg viewBox="0 0 16 16" aria-hidden="true"><circle cx="8" cy="8" r="6.5" fill="none" stroke="#663300" stroke-width="1.3"/><ellipse cx="8" cy="8" rx="3" ry="6.5" fill="none" stroke="#663300" stroke-width="1.1"/><path d="M1.5 8h13M2.5 4.8h11M2.5 11.2h11" stroke="#663300" stroke-width="1.1"/></svg>
        www.bramkeystone.com
      </li>
    </ul>

    <address class="address">
      1867 Larkspur Avenue<br>
      Millbrook, ON L0A 1G0
    </address>
  </section>
</main>
</body>
</html>
```